NEW Modern Sleek Business Card for VR Language Startup

Our startup is using VR to lead the next wave of world language education. We need a two-sided business card that introduces the larger organization (Brightloom Language Inc) and our contact info on one side and shows the product, Glimwoorld, on the other side.

Side 1 (contact info)= Brightloom Logo and Contact info (name, title, phone, email)

Side 2 (product)= Glimworld logo, text, and website
Text= Culturally Immersive Language Learning Games
Website= www.glimworld-play.com

Target Market(s)

Education, Technology

Contact Information for Business Card

Contact info will be updated upon approval of the design. For now, put this as a placeholder.

Perry Dunmore
Founder & CEO
pdunmore@quillpost-mail.net
(555)-014-2286

Font styles to use
Other font styles liked:
• Gibson and Century Gothic are the brand fonts

Requirements
Nice to have
• I would love to see cohesion between the design and colors of the two logos. I have attached a few business card designs that I like, so you can get a feel for my preferred style.

```html
<!DOCTYPE html>
<html lang="en">
<head>
<meta charset="utf-8">
<title>Brightloom Language – Business Card</title>
<link rel="stylesheet" href="https://fonts.googleapis.com/css2?family=Montserrat:wght@500;600;700&family=Didact+Gothic&display=swap">
<style>
  :root {
    --page-bg: #e4e4e6;
    --card-white: #f3f3f4;
    --ink: #1d1d1f;
    --ink-soft: #3a3a3c;
    --white: #ffffff;
    --orange: #e98a2f;
    --red: #e4303f;
    --violet: #8a4fb4;
    --blue: #4f5fdc;
    --teal: #27d8c9;
    --card-w: 770px;
    --card-h: 440px;
  }
  * { box-sizing: border-box; margin: 0; padding: 0; }
  html, body {
    width: 1200px; height: 1200px; overflow: hidden;
    background: var(--page-bg);
  }
  .sheet {
    width: 1200px; height: 1200px;
    display: flex; flex-direction: column; align-items: center; justify-content: center;
    gap: 70px;
  }
  .card {
    width: var(--card-w); height: var(--card-h);
    border-radius: 38px;
    position: relative;
    overflow: hidden;
  }
  /* Contact side */
  .card--contact { background: var(--card-white); }
  .contact-block {
    position: absolute; left: 110px; top: 150px;
  }
  .brand {
    display: flex; align-items: center; gap: 16px;
  }
  .brand-dot {
    width: 58px; height: 58px; border-radius: 50%;
    background: linear-gradient(135deg, var(--orange), var(--red) 35%, var(--violet) 60%, var(--blue) 80%, var(--teal));
  }
  .brand-name {
    font-family: "Montserrat", sans-serif;
    font-weight: 700;
    font-size: 30px;
    letter-spacing: 0.12em;
    color: var(--ink);
  }
  .person { margin-top: 34px; margin-left: 70px; font-family: "Didact Gothic", sans-serif; color: var(--ink); }
  .person-name { font-size: 36px; line-height: 1; }
  .person-title { font-size: 13px; color: var(--ink-soft); margin-top: 4px; }
  .person-contact { margin-top: 18px; font-size: 20px; line-height: 1.35; }

  /* Product side */
  .card--product {
    background: linear-gradient(158deg, var(--orange) 0%, var(--red) 34%, var(--violet) 52%, var(--blue) 72%, var(--teal) 100%);
    display: flex; flex-direction: column; align-items: center; justify-content: center;
    color: var(--white); text-align: center;
  }
  .card--product .brand-dot { background: var(--white); width: 70px; height: 70px; }
  .card--product .brand-name { color: var(--white); font-size: 38px; }
  .tagline {
    margin-top: 34px;
    font-family: "Montserrat", sans-serif; font-weight: 700;
    font-size: 22px; letter-spacing: 0.01em;
  }
  .website {
    margin-top: 12px;
    font-family: "Didact Gothic", sans-serif;
    font-size: 20px; letter-spacing: 0.04em;
  }
</style>
</head>
<body>
  <main class="sheet">
    <section class="card card--contact" aria-label="Contact side">
      <div class="contact-block">
        <div class="brand">
          <span class="brand-dot"></span>
          <span class="brand-name">BRIGHTLOOM LANGUAGE</span>
        </div>
        <div class="person">
          <p class="person-name">Perry Dunmore</p>
          <p class="person-title">Founder &amp; CEO</p>
          <p class="person-contact">pdunmore@quillpost-mail.net<br>(555)-014-2286</p>
        </div>
      </div>
    </section>

    <section class="card card--product" aria-label="Product side">
      <div class="brand">
        <span class="brand-dot"></span>
        <span class="brand-name">BRIGHTLOOM LANGUAGE</span>
      </div>
      <p class="tagline">Culturally Immersive Language Learning Games</p>
      <p class="website">www.glimworld-play.com</p>
    </section>
  </main>
</body>
</html>
```